A modern, fresh introduction to Buddhism

I need a book cover for an A6 sized book to be used both for ebook and hard copy. The author is a young, modern Buddhist teacher of high standing who has written this short intro to Buddhism in an informal Q & As format using modern, accessible language to convey profound and meaningful ideas to the general public. The author is Tibetan, but teaches worldwide and is very personable and dynamic. The cover should portray this and have a fresh yet authentic feel to it (nothing new-agey!). Please see the author's websites www.torvenmalsiteacher.org and www.vrmq.org for reference, but do not feel that the design must align completely with the website designs.

Target Market(s)

General public both in Europe and America and in Asia ranging from teenagers to the elderly. A really broad audience.

Industry/Entity Type

Teacher

Requirements
Must have
• Please include the following text that on the front cover:

A Window Onto Stillwaters

By Dorwel Tamsung Geshela

Please include the following on the back cover:

Mirun Teskavo Publications (with attached logo above it)
Nice to have
• A simplistic, artistic, and modern look without any traditional religious images.
Should not have
• No buddha images or religious images. I would prefer a more simplistic, modern and artistic look.

```html
<!DOCTYPE html>
<html lang="en">
<head>
<meta charset="utf-8">
<title>A Window Onto Stillwaters — Book Cover</title>
<link href="https://fonts.googleapis.com/css2?family=Antonio:wght@300;400;600&family=Oswald:wght@500&display=swap" rel="stylesheet">
<style>
  :root {
    --backdrop: #1f6f74;
    --sun-yellow: #f7c81a;
    --warm-orange: #f29a1c;
    --silk-magenta: #e8127f;
    --deep-magenta: #c80c6c;
    --ink: #141010;
    --paper-white: #ffffff;
    --accent-yellow: #f8e21a;
  }
  * { margin: 0; padding: 0; box-sizing: border-box; }
  html, body {
    width: 1200px;
    height: 900px;
    overflow: hidden;
    background: var(--backdrop);
  }
  .canvas {
    position: relative;
    width: 1200px;
    height: 900px;
  }
  .cover {
    position: absolute;
    left: 64px;
    top: 62px;
    width: 1072px;
    height: 753px;
    overflow: hidden;
  }
  .cover-photo {
    position: absolute;
    inset: 0;
    background:
      linear-gradient(158deg,
        var(--sun-yellow) 0%,
        var(--sun-yellow) 30%,
        var(--warm-orange) 40%,
        var(--silk-magenta) 52%,
        var(--deep-magenta) 100%);
  }
  .publisher {
    position: absolute;
    left: 22px;
    top: 190px;
    width: 170px;
    text-align: center;
    font-family: "Antonio", sans-serif;
    font-weight: 600;
    color: var(--ink);
    line-height: 1.05;
  }
  .publisher-name {
    display: block;
    font-size: 24px;
    letter-spacing: 1px;
  }
  .publisher-imprint {
    display: block;
    font-size: 12px;
    letter-spacing: 1.5px;
    margin-top: 4px;
  }
  .title-block {
    position: absolute;
    left: 588px;
    top: 346px;
  }
  .title-lead {
    font-family: "Antonio", sans-serif;
    font-weight: 300;
    font-size: 88px;
    line-height: 1;
    color: var(--ink);
    text-transform: uppercase;
    letter-spacing: 1px;
  }
  .title-main {
    font-family: "Antonio", sans-serif;
    font-weight: 300;
    font-size: 116px;
    line-height: 1;
    color: var(--paper-white);
    margin-top: 4px;
  }
  .byline {
    font-family: "Oswald", sans-serif;
    font-weight: 500;
    font-size: 28px;
    color: var(--accent-yellow);
    margin-top: 12px;
  }
  .byline-by {
    font-size: 18px;
    text-transform: uppercase;
    margin-right: 4px;
  }
</style>
</head>
<body>
  <main class="canvas">
    <section class="cover">
      <div class="cover-photo" role="img" aria-label="Photograph of flowing magenta silk fabric sweeping across a warm yellow background"></div>

      <div class="publisher">
        <span class="publisher-name">MIRUN<br>TESKAVO</span>
        <span class="publisher-imprint">PUBLICATIONS</span>
      </div>

      <div class="title-block">
        <h1>
          <span class="title-lead" style="display:block">A Window Onto</span>
          <span class="title-main" style="display:block">Stillwaters</span>
        </h1>
        <p class="byline"><span class="byline-by">By</span>Dorwel Tamsung Geshela</p>
      </div>
    </section>
  </main>
</body>
</html>
```